Dental-Specific Brochure for IT Services

We are creating a brochure for IT services for local dental practices. Highlights should include:
- no contract / we earn your business on a month to month basis
- affordable pricing
- fast response times
- 25+ local dental practices
- predictable fixed-rate billing
Text should include:
Why Dental Practices Choose WPAX?At WPAX, we specialize in providing reliable, affordable, and high-quality IT solutions tailored specifically for dental offices. With over 25 local dental practices trusting us with their IT needs, we understand the unique challenges you face and offer solutions to keep your practice running smoothly.
What Sets WPAX Apart?
✅ No Contracts – We believe in earning your business every month. Stay because you want to, not because you have to.
✅ Affordable Pricing – Cost-effective solutions that fit your budget without sacrificing quality.
✅ Fast Response Times – When you need IT support, we’re there. Minimize downtime and keep your practice operational.
✅ Predictable Fixed-Rate Billing – No surprises, just straightforward pricing that makes budgeting easy.
✅ Proven Track Record – Over 25 dental practices in the area trust WPAX for their IT support.
✅ Expert Cybersecurity & Ransomware Protection – Advanced security measures to protect patient data and experience with HIPAA HITECH Act.
✅ Full Support for Practice Management Software – We work with Hollin Dental, Murvaplex, Quavolo, and other leading platforms.
Our IT Services for Dental Practices:
VoIP Phone Solutions – Reliable communication for your front desk and patient calls.
Managed IT Support – Proactive monitoring, maintenance, and troubleshooting to prevent downtime.
Cloud Solutions – Secure, scalable storage and software solutions for your practice.
Network & Wi-Fi Optimization – Fast, secure, and reliable internet for your office.
High-Speed Fiber Internet – Ensure fast and reliable connectivity to keep your practice running smoothly.
Let’s Get Started!
Join the growing number of dental practices that trust WPAX for their IT needs. Contact us today to schedule a consultation and see how we can help your practice thrive.
-
We would like contact info displayed similarly to how it is on the other brochure in the attachments. I will also be adding some more pictures to use; feel free to add in holding spots for pictures similar to what is in the example brochure.
Logo is in attachments along with current brochure.

```html
<!DOCTYPE html>
<html lang="en">
<head>
<meta charset="utf-8">
<title>WPAX – IT Services for Dental Practices</title>
<link href="https://fonts.googleapis.com/css2?family=Montserrat:wght@300;400;500;600;700;800&family=Oswald:wght@600&display=swap" rel="stylesheet">
<style>
  :root{
    --navy:#13207a;
    --navy-deep:#0c1660;
    --green:#7dbb30;
    --green-light:#8cc63f;
    --band:#e4e6ee;
    --band-dark:#cfd0cc;
    --ink:#1e1e1e;
    --white:#ffffff;
  }
  *{margin:0;padding:0;box-sizing:border-box}
  html,body{width:876px;height:1200px;overflow:hidden;background:var(--white)}
  body{font-family:"Montserrat",sans-serif;color:var(--ink)}
  .brochure{position:relative;width:876px;height:1200px;overflow:hidden;background:var(--white)}
  .backdrop{position:absolute;inset:0}
  .brand-name{position:absolute;left:24px;top:20px;font-family:"Montserrat",sans-serif;font-weight:800;
    font-size:96px;line-height:1;color:var(--navy);letter-spacing:-2px}
  .hero-title{position:absolute;left:27px;top:248px;font-weight:800;color:var(--green-light);
    font-size:36.5px;line-height:44.5px}
  .hero-copy{position:absolute;left:27px;top:378px;width:429px;color:var(--white);font-weight:300;
    font-size:22px;line-height:27.4px;text-align:justify}
  .apart{position:absolute;left:30px;top:690px;width:445px}
  .apart h2{font-size:19.2px;font-weight:700;color:var(--ink);margin-bottom:6px;line-height:24px}
  .apart h2 span{color:var(--navy)}
  .perk{position:relative;padding-left:28px}
  .perk svg{position:absolute;left:0;top:1px;width:18px;height:18px}
  .perk h3{font-size:15.2px;font-weight:700;color:var(--green);line-height:18.2px}
  .perk p{font-size:15.2px;line-height:18.2px;font-weight:400;color:var(--ink)}
  .services{position:absolute;left:516px;top:677px;width:334px}
  .services h2{font-size:20.5px;font-weight:700;line-height:21px;color:var(--ink);margin-bottom:5px}
  .services h2 span{color:var(--navy)}
  .service h3{font-size:15px;font-weight:700;color:var(--navy);line-height:18.2px}
  .service p{font-size:15px;line-height:18.2px;color:var(--ink)}
  .divider{position:absolute;left:495px;top:831px;width:1px;height:296px;background:var(--green)}
  .cta{position:absolute;left:495px;top:1009px;width:381px;height:127px;padding:6px 10px 0 21px;
    background:linear-gradient(180deg,#e9f3dc 0%,#dcecc6 100%)}
  .cta h2{font-size:21px;font-weight:700;color:var(--navy);line-height:24px}
  .cta p{font-size:15px;line-height:18px;color:var(--ink)}
  .footer-call{position:absolute;left:27px;top:1147px;font-family:"Oswald",sans-serif;font-weight:600;
    font-size:37.8px;line-height:50px;color:var(--white);letter-spacing:-0.5px}
  .footer-contact{position:absolute;left:535px;top:1160px;font-size:16px;font-weight:600;color:var(--white);white-space:nowrap}
  .footer-contact .sep{font-weight:300;margin:0 8px}
</style>
</head>
<body>
<main class="brochure">
  <svg class="backdrop" width="876" height="1200" viewBox="0 0 876 1200">
    <defs>
      <linearGradient id="heroGrad" x1="0" y1="0" x2="1" y2="1">
        <stop offset="0" stop-color="#1a2b90"/>
        <stop offset="0.6" stop-color="#12207a"/>
        <stop offset="1" stop-color="#0b1559"/>
      </linearGradient>
      <linearGradient id="photoA" x1="0" y1="0" x2="1" y2="1">
        <stop offset="0" stop-color="#8a6a4a"/><stop offset="1" stop-color="#c9c3bb"/>
      </linearGradient>
      <linearGradient id="photoB" x1="0" y1="0" x2="1" y2="1">
        <stop offset="0" stop-color="#b07a45"/><stop offset="1" stop-color="#d7c7b0"/>
      </linearGradient>
      <linearGradient id="photoC" x1="0" y1="0" x2="1" y2="1">
        <stop offset="0" stop-color="#24307a"/><stop offset="1" stop-color="#b9b8bd"/>
      </linearGradient>
    </defs>
    <polygon points="0,179 322,179 360,130 876,130 876,585 569,585 526,636 0,636"
      fill="url(#heroGrad)" role="img" aria-label="Dental treatment room photo with a blue overlay"/>
    <polygon points="0,0 876,0 876,58 0,58" fill="var(--green)"/>
    <polygon points="0,58 876,58 876,103 346,103 310,154 0,154" fill="var(--green-light)"/>
    <polygon points="0,154 310,154 346,103 876,103 876,130 360,130 322,179 0,179" fill="var(--band)"/>
    <polygon points="0,636 526,636 569,585 876,585 876,597 586,597 544,648 0,648" fill="var(--white)"/>
    <polygon points="0,648 544,648 586,597 876,597 876,612 598,612 556,665 0,665" fill="var(--band-dark)"/>
    <polygon points="650,256 703,167 809,167 862,256 809,345 703,345" fill="url(#photoA)"
      stroke="var(--green)" stroke-width="5" role="img" aria-label="Photo of hands typing on a laptop with service icons"/>
    <polygon points="470,356 523,266 629,266 682,356 629,446 523,446" fill="url(#photoB)"
      stroke="var(--white)" stroke-width="5" role="img" aria-label="Photo of a Wi-Fi sign beside a small plant on a desk"/>
    <polygon points="650,458 703,369 809,369 862,458 809,547 703,547" fill="url(#photoC)"
      stroke="var(--green)" stroke-width="5" role="img" aria-label="Photo of a laptop showing a support screen"/>
    <polygon points="0,1142 463,1142 399,1200 0,1200" fill="var(--navy)"/>
    <polygon points="463,1142 876,1142 876,1200 399,1200" fill="var(--green-light)"/>
  </svg>

  <div class="brand-name">wpax</div>

  <h1 class="hero-title">Why<br>Dental Practices<br>Choose WPAX?</h1>
  <p class="hero-copy">At WPAX, we specialize in providing reliable, affordable, and high-quality IT solutions tailored specifically for dental offices. With over 25 local dental practices trusting us with their IT needs, we understand the unique challenges you face and offer solutions to keep your practice running smoothly.</p>

  <section class="apart">
    <h2>What Sets <span>WPAX Apart?</span></h2>
    <div class="perk">
      <svg viewBox="0 0 20 20"><circle cx="10" cy="10" r="8.5" fill="none" stroke="#7dbb30" stroke-width="2"/><path d="M5.5 10.2l3 3 6.5-7" fill="none" stroke="#7dbb30" stroke-width="2.4" stroke-linecap="round"/></svg>
      <h3>No Contracts</h3>
      <p>We believe in earning your business every month. Stay because you want to, not because you have to.</p>
    </div>
    <div class="perk">
      <svg viewBox="0 0 20 20"><circle cx="10" cy="10" r="8.5" fill="none" stroke="#7dbb30" stroke-width="2"/><path d="M5.5 10.2l3 3 6.5-7" fill="none" stroke="#7dbb30" stroke-width="2.4" stroke-linecap="round"/></svg>
      <h3>Affordable Pricing</h3>
      <p>Cost-effective solutions that fit your budget without sacrificing quality.</p>
    </div>
    <div class="perk">
      <svg viewBox="0 0 20 20"><circle cx="10" cy="10" r="8.5" fill="none" stroke="#7dbb30" stroke-width="2"/><path d="M5.5 10.2l3 3 6.5-7" fill="none" stroke="#7dbb30" stroke-width="2.4" stroke-linecap="round"/></svg>
      <h3>Fast Response Times</h3>
      <p>When you need IT support, we’re there. Minimize downtime and keep your practice operational.</p>
    </div>
    <div class="perk">
      <svg viewBox="0 0 20 20"><circle cx="10" cy="10" r="8.5" fill="none" stroke="#7dbb30" stroke-width="2"/><path d="M5.5 10.2l3 3 6.5-7" fill="none" stroke="#7dbb30" stroke-width="2.4" stroke-linecap="round"/></svg>
      <h3>Predictable Fixed-Rate Billing</h3>
      <p>No surprises, just straightforward pricing that makes budgeting easy.</p>
    </div>
    <div class="perk">
      <svg viewBox="0 0 20 20"><circle cx="10" cy="10" r="8.5" fill="none" stroke="#7dbb30" stroke-width="2"/><path d="M5.5 10.2l3 3 6.5-7" fill="none" stroke="#7dbb30" stroke-width="2.4" stroke-linecap="round"/></svg>
      <h3>Proven Track Record</h3>
      <p>Over 25 dental practices in the area trust WPAX for their IT support.</p>
    </div>
    <div class="perk">
      <svg viewBox="0 0 20 20"><circle cx="10" cy="10" r="8.5" fill="none" stroke="#7dbb30" stroke-width="2"/><path d="M5.5 10.2l3 3 6.5-7" fill="none" stroke="#7dbb30" stroke-width="2.4" stroke-linecap="round"/></svg>
      <h3>Expert Cybersecurity &amp; Ransomware Protection</h3>
      <p>Advanced security measures to protect patient data and experience with HIPAA HITECH Act.</p>
    </div>
    <div class="perk">
      <svg viewBox="0 0 20 20"><circle cx="10" cy="10" r="8.5" fill="none" stroke="#7dbb30" stroke-width="2"/><path d="M5.5 10.2l3 3 6.5-7" fill="none" stroke="#7dbb30" stroke-width="2.4" stroke-linecap="round"/></svg>
      <h3>Full Support for Practice Management Software</h3>
      <p>We work with Hollin Dental, Murvaplex, Quavolo, and other leading platforms.</p>
    </div>
  </section>

  <div class="divider"></div>

  <section class="services">
    <h2>Our IT Services for<br><span>Dental Practices:</span></h2>
    <div class="service"><h3>VoIP Phone Solutions</h3><p>Reliable communication for your front desk and patient calls.</p></div>
    <div class="service"><h3>Managed IT Support</h3><p>Proactive monitoring, maintenance, and troubleshooting to prevent downtime.</p></div>
    <div class="service"><h3>Cloud Solutions</h3><p>Secure, scalable storage and software solutions for your practice.</p></div>
    <div class="service"><h3>Network &amp; Wi-Fi Optimization</h3><p>Fast, secure, and reliable internet for your office.</p></div>
    <div class="service"><h3>High-Speed Fiber Internet</h3><p>Ensure fast and reliable connectivity to keep your practice running smoothly.</p></div>
  </section>

  <section class="cta">
    <h2>Let’s Get Started!</h2>
    <p>Join the growing number of dental practices that trust WPAX for their IT needs. Contact us today to schedule a consultation and see how we can help your practice thrive.</p>
  </section>

  <div class="footer-call">CALL NOW 555-014-2290</div>
  <div class="footer-contact">sales@wpaxit.com<span class="sep">|</span>www.wpaxit.com</div>
</main>
</body>
</html>
```